Road Construction Company needs business cards

We would like a new business card designed for our business.

We're a road construction company based in Qld, Australia.

Can the business card please have the following information on it.

Name: Warren Halbeck
Position: General Manager
Phone: 0472 915 348
Email: Warren.halbeck@tovrin.com.au
Address: 87 Marrow Ave, Pendlebay, QLD, 4023
Website: www.tovrin.com.au

Visually we'd like the card to be professional and simple.

Attached is our logo.

Our website is www.tovrin.com.au

Target Market(s)

Men aged 25-60

Contact Information for Business Card

As listed in project description

Font styles to use
Serif

Requirements
Must have
• Large logo on back of card

```html
<!DOCTYPE html>
<html lang="en">
<head>
<meta charset="utf-8">
<title>Tovrin – Business Card</title>
<link rel="stylesheet" href="https://fonts.googleapis.com/css2?family=Open+Sans:wght@400;600;700;800&display=swap">
<style>
  :root {
    --backdrop: #4b4b4b;
    --card: #ffffff;
    --navy: #1254a5;
    --sky: #44aadb;
    --ink: #1b1b1b;
  }
  html, body {
    margin: 0;
    padding: 0;
    width: 1200px;
    height: 780px;
    overflow: hidden;
    background: var(--backdrop);
    font-family: "Open Sans", Arial, sans-serif;
  }
  .sheet {
    position: relative;
    width: 1200px;
    height: 780px;
    display: flex;
    align-items: center;
    justify-content: center;
    gap: 40px;
  }
  .card {
    position: relative;
    width: 540px;
    height: 309px;
    background: var(--card);
    overflow: hidden;
    box-shadow: 0 6px 18px rgba(0,0,0,.35);
  }
  .card-bands {
    position: absolute;
    inset: 0;
    width: 100%;
    height: 100%;
  }
  .band-navy { fill: var(--navy); }
  .band-sky { fill: var(--sky); }

  /* back */
  .brand-large {
    position: absolute;
    left: 0; right: 0;
    top: 112px;
    text-align: center;
    font-weight: 800;
    font-size: 74px;
    letter-spacing: 2px;
    color: var(--navy);
    line-height: 1;
  }

  /* front */
  .brand-small {
    position: absolute;
    left: 36px;
    top: 130px;
    width: 190px;
    text-align: center;
    font-weight: 800;
    font-size: 38px;
    letter-spacing: 1px;
    color: var(--navy);
    line-height: 1;
  }
  .divider {
    position: absolute;
    left: 248px;
    top: 62px;
    width: 2px;
    height: 168px;
    background: var(--sky);
  }
  .contact-block {
    position: absolute;
    left: 270px;
    top: 58px;
    color: var(--ink);
  }
  .person-name {
    margin: 0;
    font-weight: 700;
    font-size: 21px;
    color: var(--navy);
    text-transform: uppercase;
    line-height: 1.1;
  }
  .person-role {
    margin: 1px 0 10px;
    font-weight: 700;
    font-size: 12.5px;
  }
  .address {
    margin: 0 0 10px;
    font-size: 12.5px;
    line-height: 1.35;
  }
  .contact-list {
    list-style: none;
    margin: 0;
    padding: 0;
    font-size: 12.5px;
    line-height: 1.5;
  }
  .contact-list li {
    display: flex;
    align-items: center;
    gap: 8px;
  }
  .icon {
    width: 12px;
    height: 12px;
    flex: none;
  }
  .icon path, .icon circle, .icon rect { fill: none; stroke: var(--sky); stroke-width: 1.6; }
  .icon .solid { fill: var(--sky); stroke: none; }
</style>
</head>
<body>
<main class="sheet">

  <section class="card card-back" aria-label="Card back">
    <svg class="card-bands" viewBox="0 0 540 309" preserveAspectRatio="none" aria-hidden="true">
      <polygon class="band-sky" points="540,190 540,214 430,309 400,309"/>
      <polygon class="band-navy" points="0,292 250,292 232,309 0,309"/>
    </svg>
    <div class="brand-large">TOVRIN</div>
  </section>

  <section class="card card-front" aria-label="Card front">
    <svg class="card-bands" viewBox="0 0 540 309" preserveAspectRatio="none" aria-hidden="true">
      <polygon class="band-sky" points="330,270 540,262 540,282 360,282"/>
      <polygon class="band-navy" points="0,292 305,286 345,296 345,309 0,309"/>
    </svg>

    <div class="brand-small">TOVRIN</div>
    <div class="divider"></div>

    <div class="contact-block">
      <h1 class="person-name">Warren Halbeck</h1>
      <p class="person-role">General Manager</p>
      <p class="address">87 Marrow Ave,<br>Pendlebay, QLD, 4023</p>
      <ul class="contact-list">
        <li>
          <svg class="icon" viewBox="0 0 12 12" aria-hidden="true"><path class="solid" d="M2.4 1 4.3 3.2 3.3 4.4C4 6 5.8 7.8 7.5 8.6L8.7 7.6 11 9.5 9.9 11C5.5 10.6 1.3 6.4 1 2.1Z"/></svg>
          <span>0472 915 348</span>
        </li>
        <li>
          <svg class="icon" viewBox="0 0 12 12" aria-hidden="true"><circle cx="6" cy="6" r="5"/><path d="M1 6H11M6 1C3.5 4 3.5 8 6 11M6 1C8.5 4 8.5 8 6 11"/></svg>
          <span>www.tovrin.com.au</span>
        </li>
        <li>
          <svg class="icon" viewBox="0 0 12 12" aria-hidden="true"><rect x="1" y="2.5" width="10" height="7"/><path d="M1 2.5 6 6.5 11 2.5"/></svg>
          <span>Warren.halbeck@tovrin.com.au</span>
        </li>
      </ul>
    </div>
  </section>

</main>
</body>
</html>
```